Schlichtes Design für Malerbetrieb
Zielgruppe
Wir sind ein mittelgroßer Malerbetrieb in München mit umfangreichem Leistungsspektrum.
Unsere Hauptleistungen sind: Fassadenrenovierung, Altbausanierung, Betoninstandsetzung, Balkonabdichtung (kein Neubau!).
Unsere Zielgruppen sind: Hausverwaltungen, Firmen und Privatpersonen.
Unsere Kunden schätzen: Konstruktive Organisation und Planung im Vorfeld, Zuverlässigkeit, saubere Arbeitsweise, dauerhafte Balkonabdichtungen.
Aufgabenstellung
Wir möchten eine langlebige, stilvolle, minimalistische Homepage.
Wir möchten von der bestehenden Homepage nur die Schriftart für unseren Firmennamen (Century Gothic) und wenn möglich (nicht zwingend), irgendwo das florale Muster einbauen. Corporate-Design haben wir nicht.
Farbtöne: Firmennamen Orange (hellorange bis erdiges Orange möglich, da sind wir nicht fixiert) , einen dunklen Hintergrundfarbton (Petrol-Blaugrau ?) mit gelbem (neon bis senfgelb) Akzent (Linien), Blumenmuster weiß, grau.
Dies sind nur unsere Ideen. Wir sind aber auch absolut offen für eure Profi-Ideen.
Wir möchten uns von den unzähligen langweiligen 'Pinselseiten mit veralteten Bilder' unserer Kollegen interessant und mit Stil abheben.
Eher nach dem Motto 'weniger ist mehr'.
Einen positiven, sympathischen Eindruck geben und unsere Leistungen in den Vordergrund bringen.
Da wir viele Stammkunden haben, betreiben wir kein Social-Media und möchten dies vorerst auch nicht tun.
Die Seite wird in den nächsten Jahren nicht verändert, höchstens die Bilder aktualisiert.
Die Texte haben wir alle selbst entworfen und möchten wir so übernehmen.
Die Galerien sollen unkompliziert anzuschauen sein.
Uns gefällt die Struktur und Schlichtheit von https://vaartmolen.nl/ oder Timbra.de gut und wir mögen Vintage-Grafiken gerne.
Einerseits darf die Seite geradlinig, andererseits aber auch rund und floral wirken.

```html
<!DOCTYPE html>
<html lang="de">
<head>
<meta charset="utf-8">
<title>Malerarbeiten</title>
<link rel="stylesheet" href="https://fonts.googleapis.com/css2?family=Oswald:wght@300&family=Arimo:wght@400&display=swap">
<style>
  :root {
    --white: #ffffff;
    --ink: #3a3a3a;
    --accent: #5aa3bd;
    --sky: #b3d8e2;
    --teal: #7dbdcd;
    --stone: #8a8a8a;
    --charcoal: #3c3c3c;
    --caption: #ffffff;
  }
  * { box-sizing: border-box; margin: 0; padding: 0; }
  html, body { width: 1200px; height: 900px; overflow: hidden; background: var(--white); }
  body { position: relative; font-family: "Arimo", Arial, sans-serif; }

  .site-header {
    position: absolute; top: 0; left: 0; width: 1200px; height: 120px;
    background: var(--white); z-index: 2;
  }
  .main-nav {
    position: absolute; top: 61px; left: 30px; right: 19px;
    display: flex; justify-content: space-between;
  }
  .main-nav a {
    font-family: "Oswald", "Arial Narrow", sans-serif; font-weight: 300;
    font-size: 20px; letter-spacing: 1.5px; text-transform: uppercase;
    color: var(--ink); text-decoration: none; line-height: 1;
    white-space: nowrap;
  }
  .main-nav a.is-active { color: var(--accent); }

  .gallery {
    position: absolute; top: 120px; left: 0; width: 1200px; height: 718px;
    overflow: hidden; background: var(--sky);
  }
  .gallery-backdrop { position: absolute; inset: 0; width: 100%; height: 100%; }

  .project { position: absolute; }
  .project-photo { display: block; width: 100%; }
  .project-caption {
    position: absolute; left: 0; color: var(--caption);
    font-size: 15px; line-height: 21px; white-space: nowrap;
  }

  .project--square { left: 59px; top: 154px; width: 604px; }
  .project--square .project-photo {
    height: 402px;
    background: linear-gradient(180deg, #9cc6e6 0%, #c9b27a 30%, #d8c9a4 62%, #8e8e8a 82%, #b6b4ae 100%);
  }
  .project--square .project-caption { top: 423px; }

  .project--top { left: 677px; top: 0; width: 463px; }
  .project--top .project-photo {
    height: 155px;
    background: linear-gradient(180deg, #d6d4d0 0%, #c4c2be 70%, #5f5f60 100%);
  }
  .project--top .project-caption { top: 177px; left: 6px; }

  .project--tall { left: 677px; top: 326px; width: 463px; }
  .project--tall .project-photo {
    height: 460px;
    background: linear-gradient(100deg, #e0b690 0%, #e8c7a6 45%, #cfe6f2 85%, #e4f1f7 100%);
  }

  .site-footer {
    position: absolute; top: 838px; left: 0; width: 1200px; height: 62px;
    background: var(--white);
  }
  .footer-nav {
    position: absolute; right: 25px; top: 22px; display: flex; gap: 17px;
  }
  .footer-nav a {
    font-family: "Oswald", "Arial Narrow", sans-serif; font-weight: 300;
    font-size: 19px; letter-spacing: 0.8px; text-transform: uppercase;
    color: var(--ink); text-decoration: none; line-height: 1;
  }
</style>
</head>
<body>
  <header class="site-header">
    <nav class="main-nav">
      <a href="#" class="is-active">Malerarbeiten</a>
      <a href="#">Betoninstandsetzung</a>
      <a href="#">Balkonabdichtung</a>
      <a href="#">Farbgestaltung</a>
      <a href="#">Wärmedämmung</a>
      <a href="#">Ausbildung</a>
      <a href="#">Portrait</a>
    </nav>
  </header>

  <main class="gallery">
    <svg class="gallery-backdrop" viewBox="0 0 1024 613" preserveAspectRatio="none" aria-hidden="true">
      <polygon fill="var(--teal)" points="560,240 1024,140 1024,350 700,230"/>
      <polygon fill="var(--stone)" points="0,26 340,132 1024,400 1024,613 0,613"/>
      <polygon fill="var(--charcoal)" points="0,346 565,292 1024,440 1024,613 0,613"/>
      <polygon fill="var(--teal)" points="640,222 1024,150 1024,345 820,290"/>
    </svg>

    <figure class="project project--top">
      <div class="project-photo" role="img" aria-label="Foto: renovierte helle Altbaufassade mit Balkon und Holztür, Autos davor"></div>
      <figcaption class="project-caption">Renovierung einer stark<br>verschmutzen Altbaufassade</figcaption>
    </figure>

    <figure class="project project--square">
      <div class="project-photo" role="img" aria-label="Foto: sandfarbenes Eckgebäude an einer Kreuzung mit Kirchtürmen im Hintergrund"></div>
      <figcaption class="project-caption">Renovierung einer stark<br>verschmutzen Altbaufassade</figcaption>
    </figure>

    <figure class="project project--tall">
      <div class="project-photo" role="img" aria-label="Foto: apricotfarbener Erker mit Kuppeldach und Stuckornamenten vor blauem Himmel"></div>
    </figure>
  </main>

  <footer class="site-footer">
    <nav class="footer-nav">
      <a href="#">Kontakt</a>
      <a href="#">Impressum</a>
      <a href="#">Datenschutz</a>
    </nav>
  </footer>
</body>
</html>
```